New Business Card for Software Company

We are looking at rebranding a 10 year old company that specializes in PDF and DWF solutions for Architects and Engineers. We will attach the new company logo that we are going with so you can work with that and complimentary colors.
The sample information we would like on the business card is:
Gerald Pinfold
Vice President
4738 W. Harrowgate Lane. STE 305
PMB#417
Mesa, AZ 85374
866-392-5074 US Toll Free
123-456-3190 Cell
gpinfold@plavorix.com
The old tag line that we had on the business cars was.
Delivering Dependable Drawing and Document Tools to Design Teams Everywhere.
If you have an idea for a better tag line we are open to that also.
Updates
We would like to thank all of the Designers for their wonderful work. We apologize that we will not have the time to provide feedback to everyone. There is just so many innovative and professional designs that you have all created making our decision even harder.
Target Market(s)
Architects and Engineers
Industry/Entity Type
Business
Look and feel

```html
<!DOCTYPE html>
<html lang="en">
<head>
<meta charset="utf-8">
<title>Plavorix Business Card</title>
<link rel="stylesheet" href="https://fonts.googleapis.com/css2?family=Arimo:wght@400;700&family=PT+Sans&display=swap">
<style>
  :root {
    --bg: #ecebe8;
    --card: #ffffff;
    --orange: #f26a1b;
    --orange-light: #f9a12a;
    --red: #d8342e;
    --red-dark: #c22a2e;
    --ink: #555558;
    --ink-soft: #6d6d70;
    --rule: #b9b9bb;
  }
  * { box-sizing: border-box; margin: 0; padding: 0; }
  html, body { width: 1200px; height: 720px; overflow: hidden; }
  body {
    background: var(--bg);
    font-family: "Arimo", Arial, sans-serif;
    position: relative;
  }
  .card {
    position: absolute;
    top: 205px;
    width: 540px;
    height: 309px;
    background: var(--card);
    box-shadow: 0 2px 10px rgba(0,0,0,.12);
    overflow: hidden;
  }
  .card--front { left: 40px; }
  .card--back { left: 620px; }

  .brand {
    position: absolute;
    display: flex;
    align-items: center;
    gap: 14px;
  }
  .brand__dot {
    border-radius: 50%;
    background: var(--orange);
    flex: none;
  }
  .brand__name {
    font-weight: 700;
    color: var(--orange);
    letter-spacing: -1px;
    line-height: 1;
  }
  .card--front .brand { left: 80px; top: 42px; }
  .card--front .brand__dot { width: 56px; height: 56px; }
  .card--front .brand__name { font-size: 66px; }

  .person {
    position: absolute;
    right: 285px;
    top: 178px;
    text-align: right;
  }
  .person__name { color: var(--orange); font-weight: 700; font-size: 19px; }
  .person__title { color: var(--ink-soft); font-size: 13px; margin-top: 2px; }

  .divider {
    position: absolute;
    left: 268px;
    top: 140px;
    width: 1px;
    height: 96px;
    background: var(--rule);
  }
  .contacts {
    position: absolute;
    left: 278px;
    top: 146px;
    list-style: none;
  }
  .contacts li {
    display: flex;
    align-items: center;
    gap: 8px;
    font-size: 14px;
    color: var(--ink);
    height: 25px;
  }
  .contacts svg { width: 12px; height: 12px; flex: none; }

  .accent-band {
    position: absolute;
    left: 268px;
    right: 0;
    top: 236px;
    height: 12px;
    background: linear-gradient(90deg, var(--orange), var(--orange-light));
  }
  .address-band {
    position: absolute;
    left: 0;
    right: 0;
    top: 262px;
    height: 36px;
    background: linear-gradient(90deg, var(--red), var(--red-dark));
    color: #fff;
    font-size: 15px;
    display: flex;
    align-items: center;
    padding-left: 26px;
    letter-spacing: .2px;
  }

  .card--back .brand { left: 50%; top: 92px; transform: translateX(-50%); }
  .card--back .brand__dot { width: 62px; height: 62px; }
  .card--back .brand__name { font-size: 76px; }
  .tagline {
    position: absolute;
    left: 0;
    right: 0;
    top: 196px;
    text-align: center;
    font-family: "PT Sans", Arial, sans-serif;
    font-size: 18px;
    line-height: 1.25;
    color: var(--ink);
  }
</style>
</head>
<body>
  <section class="card card--front" aria-label="Business card front">
    <div class="brand">
      <span class="brand__dot"></span>
      <span class="brand__name">plavorix</span>
    </div>
    <div class="person">
      <p class="person__name">Gerald Pinfold</p>
      <p class="person__title">Vice President</p>
    </div>
    <span class="divider"></span>
    <ul class="contacts">
      <li>
        <svg viewBox="0 0 12 12" aria-hidden="true"><path d="M2.5 1 L4.5 1 L5.2 3.5 L4 4.5 Q5 6.8 7.5 8 L8.5 6.8 L11 7.5 L11 9.5 Q10.5 11 9 11 Q1 10 1 2.8 Q1 1.3 2.5 1 Z" fill="var(--orange)"/></svg>
        866-392-5074(US) TF
      </li>
      <li>
        <svg viewBox="0 0 12 12" aria-hidden="true"><rect x="3" y="0.5" width="6" height="11" rx="1.2" fill="var(--orange)"/><rect x="4" y="2" width="4" height="6" fill="#fff"/></svg>
        123-456-3190
      </li>
      <li>
        <svg viewBox="0 0 12 12" aria-hidden="true"><rect x="0.5" y="2.5" width="11" height="7.5" rx="1" fill="var(--orange)"/><path d="M1 3 L6 7 L11 3" stroke="#fff" stroke-width="1" fill="none"/></svg>
        gpinfold@plavorix.com
      </li>
    </ul>
    <span class="accent-band"></span>
    <p class="address-band">4738 W. Harrowgate Lane. STE 305, PMB#417, Mesa, AZ 85374</p>
  </section>

  <section class="card card--back" aria-label="Business card back">
    <div class="brand">
      <span class="brand__dot"></span>
      <span class="brand__name">plavorix</span>
    </div>
    <p class="tagline">Delivering Dependable Drawing and Document Tools<br>to Design Teams Everywhere</p>
  </section>
</body>
</html>
```